Unique Business Card Design

Unique Business Card design for our orthotic and prosthetic company. Our logo is on our website, color is light blue. Unique shape (artificial leg shaped, vertical, etc..) preferred. Logo, business name, individual name and basic demographics needed.

Industry/Entity Type

Business

Contact Information for Business Card

Logo, Industry, Phone # Logo, "Prosthetic & Orthotic Services" Place to add individual name and contact info

Colors
cee9f5

Requirements
Must have
• The icon must be there, placement of "Prosthetic & Orthotic Services" can be moved
Nice to have
• Like the mix of light blue, and a little darker blue. One design included the icons from my website which was a nice touch

```html
<!DOCTYPE html>
<html lang="en">
<head>
<meta charset="utf-8">
<title>Limbwell Inc. Business Card</title>
<link href="https://fonts.googleapis.com/css2?family=Open+Sans:wght@400;600&family=Crimson+Text:ital@1&display=swap" rel="stylesheet">
<style>
  :root {
    --brand-blue: #1560ae;
    --faint-blue: #e8eef6;
    --ink-gray: #4a4a4a;
    --band-gray: #58595b;
    --paper: #ffffff;
    --backdrop: #e6e7e9;
  }
  * { margin: 0; padding: 0; box-sizing: border-box; }
  html, body {
    width: 1105px; height: 1200px; overflow: hidden;
    background: var(--backdrop);
    font-family: "Open Sans", Arial, sans-serif;
  }
  .canvas { position: relative; width: 1105px; height: 1200px; }
  .card {
    position: absolute; left: 193px; width: 720px; height: 410px; overflow: hidden;
  }
  .card-front { top: 167px; background: var(--paper); }
  .card-back { top: 623px; background: var(--brand-blue); }

  .faint-disc {
    position: absolute; left: 373px; top: -1px; width: 400px; height: 400px;
    border-radius: 50%; background: var(--faint-blue);
  }
  .brand-mark {
    position: absolute; border-radius: 50%;
  }
  .card-front .brand-mark { left: 156px; top: 61px; width: 108px; height: 108px; background: var(--brand-blue); }
  .card-back .brand-mark { left: 138px; top: 148px; width: 116px; height: 116px; background: var(--paper); }

  .brand-lockup { position: absolute; }
  .card-front .brand-lockup { left: 288px; top: 72px; color: var(--brand-blue); }
  .card-back .brand-lockup { left: 284px; top: 148px; color: var(--paper); }
  .brand-name {
    font-weight: 600; font-size: 29px; letter-spacing: 0.3px; line-height: 36px; white-space: nowrap;
  }
  .brand-rule { height: 2px; background: currentColor; margin-top: 2px; }
  .card-back .brand-rule { height: 4px; }
  .brand-tagline {
    font-family: "Crimson Text", Georgia, serif; font-style: italic;
    font-size: 18px; line-height: 24px; text-align: center; white-space: nowrap;
  }

  .person-name {
    position: absolute; left: 0; right: 0; top: 226px; text-align: center;
    color: var(--brand-blue); font-weight: 600; font-size: 26px; letter-spacing: 0.3px;
  }
  .person-name .credentials { font-size: 17px; }
  .email-row {
    position: absolute; left: 44px; width: 636px; top: 260px;
    display: flex; align-items: center; gap: 6px; color: var(--ink-gray); font-size: 18px;
  }
  .email-row::before, .email-row::after {
    content: ""; flex: 1; height: 1.5px; background: var(--brand-blue);
  }
  .contact-list, .address-list {
    position: absolute; top: 293px; list-style: none; color: var(--ink-gray); font-size: 18px; line-height: 28px;
  }
  .contact-list { left: 42px; }
  .contact-list li { display: flex; align-items: center; gap: 10px; }
  .contact-list svg { width: 18px; height: 18px; fill: var(--brand-blue); }
  .address-list { right: 40px; text-align: right; }

  .band { position: absolute; bottom: 0; height: 14px; }
  .band-blue { left: 0; width: 357px; background: var(--brand-blue); }
  .band-gray { left: 361px; right: 0; background: var(--band-gray); }
</style>
</head>
<body>
<main class="canvas">
  <section class="card card-front" aria-label="Card front">
    <div class="faint-disc"></div>
    <div class="brand-mark"></div>
    <div class="brand-lockup">
      <div class="brand-name">LIMBWELL INC.</div>
      <div class="brand-rule"></div>
      <div class="brand-tagline">Prosthetic &amp; Orthotic Services</div>
    </div>
    <h1 class="person-name">MIRIAM CALDER, <span class="credentials">CO LPO</span></h1>
    <p class="email-row">mcalder@limbwellinc.com</p>
    <ul class="contact-list">
      <li><svg viewBox="0 0 24 24"><path d="M6.6 10.8a15.1 15.1 0 0 0 6.6 6.6l2.2-2.2c.3-.3.7-.4 1-.2 1.1.4 2.3.6 3.6.6.6 0 1 .4 1 1V20c0 .6-.4 1-1 1A17 17 0 0 1 3 4c0-.6.4-1 1-1h3.5c.6 0 1 .4 1 1 0 1.3.2 2.5.6 3.6.1.3 0 .7-.2 1z"/></svg>555.214.3300</li>
      <li><svg viewBox="0 0 24 24"><path d="M7 1h10a2 2 0 0 1 2 2v18a2 2 0 0 1-2 2H7a2 2 0 0 1-2-2V3a2 2 0 0 1 2-2zm0 3v14h10V4zm5 15.5a1.2 1.2 0 1 0 0 2.4 1.2 1.2 0 0 0 0-2.4z"/></svg>555.214.3318</li>
      <li><svg viewBox="0 0 24 24"><path d="M6 2h9l3 3v5H6zm-2 9h16a2 2 0 0 1 2 2v8H2v-8a2 2 0 0 1 2-2zm2 4v2h3v-2zm5 0v2h3v-2zm5 0v2h3v-2z"/></svg>555-4870216</li>
    </ul>
    <ul class="address-list">
      <li>2290 Harbor Ave.</li>
      <li>Easton, NY 10984</li>
      <li>www.limbwellinc.com</li>
    </ul>
    <div class="band band-blue"></div>
    <div class="band band-gray"></div>
  </section>

  <section class="card card-back" aria-label="Card back">
    <div class="brand-mark"></div>
    <div class="brand-lockup">
      <div class="brand-name">LIMBWELL INC.</div>
      <div class="brand-rule"></div>
      <div class="brand-tagline">Prosthetic &amp; Orthotic Services</div>
    </div>
  </section>
</main>
</body>
</html>
```